3 in 1 website - Property Lens Works + Keepsake Harbor LLC + Marla's Game Shots

Help me simplify and organize my business life. I am a sports photographer (action, individual and teams), real estate photographer (stills and drones) and I transfer videos and photos to jump drives, along with photo restoration, etc. Currently, I have a functioning website for the transfer/restoration business at KeepsakeHarborLLC.example which was recently created and I like it. I have received several really good ideas for the Real Estate Photography portion! I don't have anything started for the Sports Pics. My vision possibly includes a main/home page giving people the option to choose real estate, sports or transfer/restoration. I just want them combined into one site....somehow to better organize my businesses and give me ONE place to keep to updated and check for communication. I just updated the brief again and added logo files for my "parent" company called "Keepsake Harbor". I prefer this logo at the top of the main/home page, please. I previously uploaded the logo for Property Lens Works which would be used with the real estate portion of my business. At this point, I don't have a logo for the sports photography portion.

Target Market(s)

Real Estate Agents and Brokers; Sports team, parents and boosters; Community members typically 40+ years old

Industry/Entity Type

Real Estate Photography; Local sports teams; Community members 40+ years old

Coding

Coded - Design and coding required

Number of Pages Required

3 page

Requirements
Must have
• At least one page for each area: real estate, sports, digital transfers. The real estate will need to connect to an account I have with QLN for checkout options. The sports page(s) will need to connect to a 3rd party service, also. The digital transfers, photo restorations, etc. would just need a way for them to request service.
Nice to have
• I currently have a website at KeepsakeHarborLLC.example for the digital transfer/photo restoration part of my business. I like this website but want it integrated with one main site for all 3 businesses.

```html
<!DOCTYPE html>
<html lang="en">
<head>
<meta charset="utf-8">
<title>Property Lens Works – Real Estate Photography by Keepsake Harbor LLC</title>
<link href="https://fonts.googleapis.com/css2?family=Lexend+Zetta:wght@200;300&family=Roboto:wght@400;500;700&display=swap" rel="stylesheet">
<style>
:root{
  --red:#e8252b;
  --blue:#0f6cc2;
  --ink:#222;
  --muted:#666;
  --pale:#eaf2fa;
  --white:#fff;
  --black:#000;
}
*{box-sizing:border-box;margin:0;padding:0}
html,body{width:1200px;height:4070px;overflow:hidden}
body{font-family:"Roboto",sans-serif;color:var(--ink);background:var(--white);position:relative}
a{text-decoration:none}
.abs{position:absolute}
.display{font-family:"Lexend Zetta",sans-serif;font-weight:200;letter-spacing:-2px;text-transform:uppercase}
.skew-btn{position:absolute;display:flex;align-items:center;justify-content:center;font-weight:700;color:var(--white);background:var(--red);clip-path:polygon(8% 0,100% 0,92% 100%,0 100%);font-size:16px}

/* header */
.top-rule{position:absolute;left:0;top:0;width:1200px;height:4px;background:var(--red);z-index:5}
.site-header{position:absolute;left:0;top:4px;width:1200px;height:108px;background:var(--white);z-index:3}
.site-header a{color:#333;font-size:15px}
.contact-line{position:absolute;top:22px;display:flex;align-items:center;gap:14px;font-size:15px;color:#555}
.nav-left,.nav-right{position:absolute;top:67px;display:flex}
.nav-left a{margin-right:54px}
.nav-right a{margin-left:32px}
.brand-tab{position:absolute;left:430px;top:4px;width:340px;height:156px;background:var(--white);clip-path:polygon(0 0,100% 0,88% 100%,12% 100%);display:flex;align-items:center;justify-content:center;z-index:4}
.brand-name{font-weight:700;color:var(--red);font-size:22px;text-align:center;line-height:1.15;display:flex;align-items:center;gap:9px}
.brand-mark{width:14px;height:14px;border-radius:50%;background:var(--red);flex:none}

/* hero */
.hero{position:absolute;left:0;top:112px;width:1200px;height:661px;background:radial-gradient(ellipse at 50% 35%,#3b4a5a 0%,#262a30 45%,#141517 100%)}
.hero h1{position:absolute;top:418px;width:100%;text-align:center;color:var(--white);font-size:36px;line-height:46px}

/* about */
.about h2{position:absolute;left:111px;top:874px;font-size:34px}
.about p{position:absolute;left:111px;top:936px;width:432px;font-size:15px;line-height:26.5px;color:var(--muted)}
.about ul{position:absolute;left:162px;top:1055px;list-style:none;font-size:15px;color:var(--muted)}
.about li{height:29.5px;display:flex;align-items:center;gap:10px}
.about li::before{content:"";width:12px;height:12px;border-radius:50%;border:2px solid #888;box-shadow:inset 0 0 0 2px #fff;background:#888;margin-left:-24px}
.person{position:absolute;left:111px;top:1159px;font-weight:500;font-size:17px}
.role{position:absolute;left:111px;top:1189px;font-size:13.5px;color:var(--muted)}
.about-block{position:absolute;left:599px;top:930px;width:491px;height:302px;background:var(--blue)}
.about-photo{position:absolute;left:647px;top:882px;width:395px;height:395px;background:linear-gradient(160deg,#b9c4cf 0%,#5a6f86 45%,#33465c 100%);box-shadow:0 4px 14px rgba(0,0,0,.4)}

/* pricing */
.pricing{position:absolute;left:0;top:1390px;width:1200px;height:1080px;background:var(--pale)}
.pricing h2{position:absolute;top:84px;width:100%;text-align:center;font-size:34px}
.tab{position:absolute;top:155px;width:162px;height:46px;display:flex;align-items:center;justify-content:center;font-size:16px}
.tab.on{left:423px;background:var(--blue);color:var(--white)}
.tab.off{left:611px;border:1px solid var(--blue);color:var(--blue);background:var(--white)}
.plan-photo{position:absolute;top:253px;width:314px;height:395px;border:4px solid var(--white);box-shadow:0 2px 8px rgba(0,0,0,.2)}
.plan{position:absolute;top:378px;width:288px;height:537px;background:var(--white);box-shadow:0 2px 10px rgba(0,0,0,.08);padding:30px 0 0 26px}
.plan h3{color:var(--blue);font-weight:500;font-size:16.5px;text-align:center;margin-left:-26px}
.plan .price{font-size:22px;text-align:center;margin:12px 0 14px -26px;color:#333}
.plan ul{list-style:none;font-size:13px;color:var(--muted);line-height:18px}
.plan li{display:flex;gap:9px;margin-bottom:13px;padding-right:30px}
.plan li svg{flex:none;margin-top:2px}
.plan .skew-btn{left:60px;bottom:-19px;width:166px;height:42px}
.more{position:absolute;left:500px;top:978px;width:200px;height:42px;display:flex;align-items:center;justify-content:center;color:var(--red);font-weight:700;font-size:16px}

/* portfolio */
.portfolio{position:absolute;left:0;top:2470px;width:1200px;height:697px;background:linear-gradient(180deg,#1472c6,#0d63b5)}
.portfolio h2{position:absolute;top:70px;width:100%;text-align:center;color:var(--white);font-size:34px}

/* contact */
.contact h2{position:absolute;top:3240px;width:100%;text-align:center;font-size:34px}
.info{position:absolute;left:122px;display:flex;gap:16px}
.info .ring{width:50px;height:50px;border-radius:50%;border:2px solid var(--red);display:flex;align-items:center;justify-content:center;flex:none}
.info h4{font-weight:500;font-size:18px;margin-top:2px}
.info span{display:block;font-size:14.5px;color:var(--muted);line-height:26px;width:240px}
.field{position:absolute;left:445px;width:318px;height:54px;background:var(--white);box-shadow:0 1px 8px rgba(0,0,0,.12);padding:17px 24px;font-size:15px;color:#999}
.message{position:absolute;left:783px;top:3315px;width:302px;height:256px;background:var(--white);box-shadow:0 1px 8px rgba(0,0,0,.12);padding:17px 24px;font-size:15px;color:#999}
.submit{left:445px;top:3520px;width:332px;height:52px;background:var(--blue);clip-path:polygon(3% 0,100% 0,97% 100%,0 100%)}

/* footer */
.site-footer{position:absolute;left:0;top:3700px;width:1200px;height:370px;background:var(--black);color:var(--white)}
.site-footer .brand-name{position:absolute;top:128px;left:0;width:100%;justify-content:center;font-size:32px}
.foot-nav{position:absolute;top:236px;width:100%;display:flex;justify-content:center;font-size:13px;font-weight:500}
.foot-nav span{margin:0 26px}
.copy{position:absolute;top:278px;width:100%;text-align:center;font-size:11px}
.social{position:absolute;top:320px;left:556px;display:flex;gap:11px}
.social i{width:22px;height:22px;border-radius:50%;background:var(--blue)}
</style>
</head>
<body>
<svg width="0" height="0" style="position:absolute">
  <symbol id="tick" viewBox="0 0 16 16"><circle cx="8" cy="8" r="6.5" fill="none" stroke="#3aa659" stroke-width="1.4"/><path d="M5 8.2l2 2 4-4.4" fill="none" stroke="#3aa659" stroke-width="1.5"/></symbol>
</svg>

<div class="top-rule"></div>
<header class="site-header">
  <div class="contact-line" style="left:127px">
    <svg width="26" height="26" viewBox="0 0 26 26"><circle cx="13" cy="13" r="13" fill="var(--blue)"/><path d="M9 7l3 3-1.5 2c1 2 2 3 4 4l2-1.5 3 3-2 2c-5 0-10-5-10-10z" fill="#fff"/></svg>
    <span>+1 555 0142-718</span>
  </div>
  <div class="contact-line" style="left:856px">
    <svg width="32" height="28" viewBox="0 0 32 28"><path d="M1 3h5l4 15h16l4-11H8" fill="none" stroke="var(--blue)" stroke-width="3"/><circle cx="12" cy="24" r="2.5" fill="var(--blue)"/><circle cx="24" cy="24" r="2.5" fill="var(--blue)"/></svg>
    <svg width="26" height="26" viewBox="0 0 26 26" style="margin-left:10px"><circle cx="13" cy="13" r="13" fill="var(--blue)"/><rect x="7" y="9" width="12" height="9" fill="none" stroke="#fff" stroke-width="1.6"/><path d="M7 9l6 5 6-5" fill="none" stroke="#fff" stroke-width="1.6"/></svg>
    <span>hello@keepsakeharbor.example</span>
  </div>
  <nav class="nav-left" style="left:127px"><a href="#">Home</a><a href="#">About Us</a><a href="#">Services</a></nav>
  <nav class="nav-right" style="left:803px"><a href="#">Packages ▾</a><a href="#">Add-Ons</a><a href="#">Contact</a></nav>
</header>
<div class="brand-tab"><div class="brand-name"><span class="brand-mark"></span>PROPERTY LENS<br>WORKS</div></div>

<section class="hero" role="img" aria-label="Dim living room interior with a large drone graphic">
  <h1 class="display">Dana Whitfield Real Estate<br>Photography</h1>
  <a class="skew-btn" style="left:518px;top:533px;width:164px;height:43px">Get A Quote</a>
</section>

<section class="about">
  <h2 class="display">About Me</h2>
  <p>Contrary to popular belief, Lorem Ipsum is not simply random text. It has roots in a piece of classical Latin literature from 45 BC, making it over 2000 years old. Harold Pennick, a Latin professor at Westbrook College</p>
  <ul><li>Lorem Ipsum is not simply random text</li><li>Lorem Ipsum is not simply random text</li><li>Lorem Ipsum is not simply random text</li></ul>
  <div class="person">Priya Marston</div>
  <div class="role">( Position Name)&nbsp;&nbsp; Dana</div>
  <a class="skew-btn" style="left:111px;top:1235px;width:167px;height:40px">Read More</a>
  <div class="about-block"></div>
  <div class="about-photo" role="img" aria-label="Portrait of a photographer holding a camera by a harbour"></div>
</section>

<section class="pricing">
  <h2 class="display">Our Pricing</h2>
  <div class="tab on">Packages</div>
  <div class="tab off">Add-Ons</div>

  <div class="plan-photo" style="left:98px;background:linear-gradient(180deg,#d8cfc4,#8a6e52)" role="img" aria-label="Modern interior with wood slat wall"></div>
  <div class="plan-photo" style="left:445px;background:linear-gradient(180deg,#e2ddd6,#b9afa2)" role="img" aria-label="White cabinetry interior"></div>
  <div class="plan-photo" style="left:788px;background:linear-gradient(180deg,#c9b796,#7a5a3a)" role="img" aria-label="Dining room with chandelier"></div>

  <div class="plan" style="left:112px">
    <h3>THE ULTIMATE PACKAGE</h3><div class="price">$150</div>
    <ul>
      <li><svg width="15" height="15"><use href="#tick"/></svg>Up to 25 ClearView+ Still Images</li>
      <li><svg width="15" height="15"><use href="#tick"/></svg>Branded &amp; Non-Branded Property Website Links</li>
      <li><svg width="15" height="15"><use href="#tick"/></svg>Company Branding</li>
      <li><svg width="15" height="15"><use href="#tick"/></svg>Agent photo &amp; contact information</li>
      <li><svg width="15" height="15"><use href="#tick"/></svg>Link to agent Property Website gallery</li>
      <li><svg width="15" height="15"><use href="#tick"/></svg>Property description &amp; details</li>
      <li><svg width="15" height="15"><use href="#tick"/></svg>Weekly Seller's report</li>
      <li><svg width="15" height="15"><use href="#tick"/></svg>Posting to MLS</li>
      <li><svg width="15" height="15"><use href="#tick"/></svg>High resolution printable still photos</li>
      <li><svg width="15" height="15"><use href="#tick"/></svg>Unlimited text updates</li>
      <li><svg width="15" height="15"><use href="#tick"/></svg>Music enabled</li>
    </ul>
    <a class="skew-btn">Choose Plan</a>
  </div>
  <div class="plan" style="left:457px">
    <h3>THE VIP PACKAGE</h3><div class="price">$200</div>
    <ul>
      <li><svg width="15" height="15"><use href="#tick"/></svg>Up to 50 ClearView+ Still Images</li>
      <li><svg width="15" height="15"><use href="#tick"/></svg>Branded &amp; Non-Branded Property Website Links</li>
      <li><svg width="15" height="15"><use href="#tick"/></svg>Company Branding</li>
      <li><svg width="15" height="15"><use href="#tick"/></svg>Agent photo &amp; contact information</li>
      <li><svg width="15" height="15"><use href="#tick"/></svg>Link to agent Property Website gallery</li>
      <li><svg width="15" height="15"><use href="#tick"/></svg>Property description &amp; details</li>
      <li><svg width="15" height="15"><use href="#tick"/></svg>Weekly Seller's report</li>
      <li><svg width="15" height="15"><use href="#tick"/></svg>Posting to MLS</li>
      <li><svg width="15" height="15"><use href="#tick"/></svg>High resolution printable still photos</li>
      <li><svg width="15" height="15"><use href="#tick"/></svg>Unlimited text updates</li>
      <li><svg width="15" height="15"><use href="#tick"/></svg>Music enabled</li>
    </ul>
    <a class="skew-btn">Choose Plan</a>
  </div>
  <div class="plan" style="left:801px">
    <h3>AERIAL DRONE PACKAGE #1</h3><div class="price">$175</div>
    <ul>
      <li><svg width="15" height="15"><use href="#tick"/></svg>Choose up to 10 Aerial Still Images</li>
      <li><svg width="15" height="15"><use href="#tick"/></svg>Branded &amp; Non-Branded Property Website Links</li>
      <li><svg width="15" height="15"><use href="#tick"/></svg>Company Branding</li>
      <li><svg width="15" height="15"><use href="#tick"/></svg>Agent photo &amp; contact information</li>
      <li><svg width="15" height="15"><use href="#tick"/></svg>Link to agent Property Website gallery</li>
      <li><svg width="15" height="15"><use href="#tick"/></svg>Property description &amp; details</li>
      <li><svg width="15" height="15"><use href="#tick"/></svg>Weekly Seller's report</li>
      <li><svg width="15" height="15"><use href="#tick"/></svg>Posting to MLS</li>
      <li><svg width="15" height="15"><use href="#tick"/></svg>High resolution printable still photos</li>
      <li><svg width="15" height="15"><use href="#tick"/></svg>Unlimited text updates</li>
      <li><svg width="15" height="15"><use href="#tick"/></svg>Music enabled</li>
    </ul>
    <a class="skew-btn">Choose Plan</a>
  </div>

  <svg class="abs" style="left:500px;top:978px" width="200" height="42"><polygon points="16,1 199,1 184,41 1,41" fill="none" stroke="var(--red)" stroke-width="1.2"/></svg>
  <a class="more">View More Plans</a>
</section>

<section class="portfolio">
  <h2 class="display">My Portfolio</h2>
  <svg class="abs" style="left:0;top:0" width="1200" height="697">
    <defs>
      <linearGradient id="city" x1="0" y1="0" x2="0" y2="1"><stop offset="0" stop-color="#9bb8d6"/><stop offset="1" stop-color="#3b5470"/></linearGradient>
      <linearGradient id="green" x1="0" y1="0" x2="1" y2="1"><stop offset="0" stop-color="#6f9a4c"/><stop offset="1" stop-color="#33592a"/></linearGradient>
      <linearGradient id="harbour" x1="0" y1="0" x2="0" y2="1"><stop offset="0" stop-color="#8fb3d8"/><stop offset=".55" stop-color="#5c7f9c"/><stop offset="1" stop-color="#5a6a3e"/></linearGradient>
      <linearGradient id="autumn" x1="0" y1="0" x2="0" y2="1"><stop offset="0" stop-color="#7d8aa0"/><stop offset="1" stop-color="#7a5a2f"/></linearGradient>
    </defs>
    <g role="img" aria-label="Gallery of aerial property and city photographs">
      <polygon points="0,162 98,162 80,382 0,382" fill="url(#city)"/>
      <polygon points="116,162 360,162 342,382 98,382" fill="#d9c9b8"/>
      <polygon points="116,162 360,162 342,382 98,382" fill="var(--red)" opacity=".82"/>
      <polygon points="368,162 616,162 598,382 350,382" fill="url(#green)"/>
      <polygon points="634,162 878,162 860,382 616,382" fill="url(#harbour)"/>
      <polygon points="342,400 588,400 570,620 324,620" fill="url(#green)"/>
      <polygon points="606,400 853,400 835,620 588,620" fill="#4f6b3a"/>
      <polygon points="871,400 1113,400 1095,620 853,620" fill="url(#autumn)"/>
      <polygon points="1131,400 1200,400 1200,620 1113,620" fill="url(#green)"/>
    </g>
    <circle cx="226" cy="264" r="9" fill="none" stroke="#fff" stroke-width="2"/><path d="M232 270l7 7" stroke="#fff" stroke-width="2"/>
  </svg>
</section>

<section class="contact">
  <h2 class="display">Contact Us</h2>
  <div class="info" style="top:3312px"><div class="ring"><svg width="16" height="20" viewBox="0 0 16 20"><path d="M8 1a6 6 0 016 6c0 5-6 12-6 12S2 12 2 7a6 6 0 016-6z" fill="var(--red)"/><circle cx="8" cy="7" r="2.2" fill="#fff"/></svg></div><div><h4>Location</h4><span>14Y, Keepsake Harbor LLC, Property Lens Works, Lorem ipsum</span></div></div>
  <div class="info" style="top:3418px"><div class="ring"><svg width="18" height="18" viewBox="0 0 26 26"><path d="M6 3l5 5-2.5 3c1.5 3 3.5 5 6.5 6.5l3-2.5 5 5-3 3C11 23 3 15 3 6z" fill="var(--red)"/></svg></div><div><h4>Phone</h4><span>+1 555 014 2718</span></div></div>
  <div class="info" style="top:3512px"><div class="ring"><svg width="18" height="14" viewBox="0 0 18 14"><rect width="18" height="14" rx="2" fill="var(--red)"/><path d="M1 2l8 6 8-6" fill="none" stroke="#fff" stroke-width="1.5"/></svg></div><div><h4>Email</h4><span>&nbsp;hello@keepsakeharbor.example</span></div></div>
  <div class="field" style="top:3315px">Name</div>
  <div class="field" style="top:3383px">Phone</div>
  <div class="field" style="top:3452px">Email</div>
  <div class="message">Type your message</div>
  <a class="skew-btn submit">Submit</a>
</section>

<footer class="site-footer">
  <div class="brand-name"><span class="brand-mark"></span>KEEPSAKE HARBOR</div>
  <nav class="foot-nav"><span>Home</span>|<span>About Us</span>|<span>Services</span>|<span>Packages</span>|<span>Add-Ons</span>|<span>Contact</span></nav>
  <div class="copy">© Copyrights 2023 Keepsake Harbor LLC – Property Lens Works | All Rights Reserved</div>
  <div class="social"><i></i><i></i><i></i></div>
</footer>
</body>
</html>
```